Interior Design/ decoration business card design

This card is for my Interior Design and Decoration business and later I will also be selling homewares. I would like the card to be very simple in design and like either white, duck egg blue , aquas or metallics on a flat mat card excellent quality card. It needs to be well designed as that is my field. I dont like fuss, the simpler the better. I would like a styalised brim under the name brim if possible. SIMPLE, STYLISH, CLASSIC, TASTEFUL

Target Market(s)

40 + year olds who are building or rennovating.

Industry/Entity Type

Business

Contact Information for Business Card

Brim
styling, design, homeware

Marnie Callow
p 0427163958
e marnie@brimhouse.com.au
w brimhouse.com.au

Requirements
Must have
• very simple, stylish, classic, sophisticated. Simple and easy to read text that is a print similar to attached image. I like simple round A's though not as in attached image.

Double sided. It wont save as double sided for some reason!!
Should not have
• not too much colour, No animated / cartoon pictures.

```html
<!DOCTYPE html>
<html lang="en">
<head>
<meta charset="utf-8">
<title>Brim – Business Card, Front and Back</title>
<link rel="stylesheet" href="https://fonts.googleapis.com/css2?family=Exo+2:wght@300;400;500&display=swap">
<style>
  :root {
    --backdrop: #6b6d70;
    --card: #ffffff;
    --ink: #2b2623;
    --ink-soft: #3d3834;
    --rule: #4a423c;
  }
  * { box-sizing: border-box; margin: 0; padding: 0; }
  html, body {
    width: 1200px;
    height: 675px;
    overflow: hidden;
    background: var(--backdrop);
    font-family: "Exo 2", sans-serif;
    color: var(--ink);
  }
  .card {
    position: absolute;
    top: 178px;
    width: 555px;
    height: 318px;
    background: var(--card);
    border-radius: 28px;
    overflow: hidden;
  }
  .card--front { left: 30px; }
  .card--back { left: 615px; }

  .card__bubble {
    position: absolute;
    inset: 0;
    width: 555px;
    height: 318px;
  }
  .brand {
    position: absolute;
    font-weight: 300;
    line-height: 1;
    color: var(--ink);
  }
  .card--front .brand {
    left: 196px;
    top: 34px;
    font-size: 64px;
    letter-spacing: 1px;
  }
  .card--back .brand {
    left: 0;
    right: 0;
    top: 104px;
    text-align: center;
    font-size: 96px;
    letter-spacing: 2px;
  }

  .person {
    position: absolute;
    right: 42px;
    top: 132px;
  }
  .person__name {
    font-size: 19px;
    font-weight: 500;
    letter-spacing: 1px;
    line-height: 1.1;
    text-transform: uppercase;
  }
  .person__role {
    font-size: 8.5px;
    font-weight: 400;
    letter-spacing: 0.8px;
    text-transform: uppercase;
    color: var(--ink-soft);
  }

  .contact {
    position: absolute;
    display: flex;
    flex-direction: column;
    gap: 10px;
    font-size: 12.5px;
    font-weight: 400;
    letter-spacing: 0.6px;
  }
  .contact__line {
    display: flex;
    align-items: center;
    gap: 9px;
    white-space: nowrap;
  }
  .contact__icon {
    width: 13px;
    height: 13px;
    flex: none;
  }
  .contact--phones { left: 36px; top: 200px; }
  .contact--web { left: 272px; top: 232px; }

  .address {
    position: absolute;
    left: 36px;
    top: 276px;
    font-size: 11.5px;
    letter-spacing: 0.6px;
    white-space: nowrap;
  }
  .divider {
    position: absolute;
    left: 250px;
    top: 206px;
    width: 3px;
    height: 62px;
    background: radial-gradient(circle, var(--ink) 1.2px, transparent 1.5px) 0 0 / 3px 7px repeat-y;
  }
</style>
</head>
<body>
  <main class="card card--front">
    <svg class="card__bubble" viewBox="0 0 555 318" aria-hidden="true">
      <path d="M165 22 H505 Q530 22 530 47 V163 Q530 188 505 188 H250 L222 224 L214 188 H165 Q140 188 140 163 V47 Q140 22 165 22 Z"
            fill="none" stroke="var(--rule)" stroke-width="2" stroke-linejoin="round"/>
    </svg>

    <h1 class="brand">brim</h1>

    <div class="person">
      <p class="person__name">Marnie Callow</p>
      <p class="person__role">General Manager</p>
    </div>

    <div class="contact contact--phones">
      <p class="contact__line">
        <svg class="contact__icon" viewBox="0 0 20 20" aria-hidden="true"><path d="M5 2 L8 2 L9 6 L7 8 Q9 12 12 13 L14 11 L18 12 L18 15 Q18 18 15 18 Q3 16 2 5 Q2 2 5 2 Z" fill="var(--ink)"/></svg>
        0427 163 958
      </p>
      <p class="contact__line">
        <svg class="contact__icon" viewBox="0 0 20 20" aria-hidden="true"><rect x="5" y="1.5" width="10" height="17" rx="2" fill="none" stroke="var(--ink)" stroke-width="1.8"/><line x1="8.5" y1="15.5" x2="11.5" y2="15.5" stroke="var(--ink)" stroke-width="1.6"/></svg>
        0427 163 958
      </p>
    </div>

    <p class="address">42 Alder Lane, Level 3, Harbour Street W.</p>

    <div class="divider" aria-hidden="true"></div>

    <div class="contact contact--web">
      <p class="contact__line">
        <svg class="contact__icon" viewBox="0 0 20 20" aria-hidden="true"><rect x="1.5" y="4" width="17" height="12" fill="var(--ink)"/><path d="M1.5 4 L10 11 L18.5 4" fill="none" stroke="#fff" stroke-width="1.4"/></svg>
        marnie@brimhouse.com.au
      </p>
      <p class="contact__line">
        <svg class="contact__icon" viewBox="0 0 20 20" aria-hidden="true"><circle cx="10" cy="10" r="8.5" fill="none" stroke="var(--ink)" stroke-width="1.6"/><ellipse cx="10" cy="10" rx="3.8" ry="8.5" fill="none" stroke="var(--ink)" stroke-width="1.3"/><line x1="1.5" y1="10" x2="18.5" y2="10" stroke="var(--ink)" stroke-width="1.3"/></svg>
        www.brimhouse.com.au
      </p>
    </div>
  </main>

  <section class="card card--back">
    <p class="brand">brim</p>
  </section>
</body>
</html>
```